Q.I.V.A. The Halbrook Grand Jury Testimony

This is the cover artwork for the audio version
of the re-creation of the Halbrook Grand Jury testimony based around the killing of Tyrell Hawkins. I need a cover for the library binders. I have the template for the binder that I can send. The title of the audio is: Q.I.V.A. I would like the words Halbrook Grand Jury Testimony added in somehow with some creative graphics. I have a website with other audio covers. I also need the words: Unabridged CD format somewhere at the bottom. Can I send the binder template later?

Target Market(s)

Audiobook

Industry/Entity Type

Audio

Font styles to use
Serif

Requirements
Nice to have
• no bullets, no blood, no dead bodies, no police, no police cars, no protest, no
• violent images, no bullets
Should not have
• nice clear sleek look

```html
<!DOCTYPE html>
<html lang="en">
<head>
<meta charset="utf-8">
<title>Q.I.V.A. — Halbrook Grand Jury Testimony</title>
<link rel="stylesheet" href="https://fonts.googleapis.com/css2?family=Tinos:ital,wght@0,400;0,700;1,700&display=swap">
<style>
  :root {
    --bg-light: #dc9158;
    --bg-mid: #c7692c;
    --bg-dark: #a9481a;
    --ink: #573129;
    --white: #ffffff;
    --gold: #f2b51c;
  }
  html, body {
    margin: 0;
    padding: 0;
    width: 1200px;
    height: 1200px;
    overflow: hidden;
  }
  .cover {
    position: relative;
    width: 1200px;
    height: 1200px;
    background: radial-gradient(ellipse 60% 55% at 50% 52%, var(--bg-light) 0%, var(--bg-mid) 55%, var(--bg-dark) 100%);
  }
  .cover-art {
    position: absolute;
    inset: 0;
    width: 1200px;
    height: 1200px;
    font-family: "Tinos", "Times New Roman", serif;
  }
  .frame { fill: none; stroke: var(--white); stroke-width: 2.5; }
  .series-title { font-weight: 700; font-size: 104px; fill: var(--ink); }
  .place { font-weight: 700; font-size: 136px; fill: var(--ink); }
  .initial { font-weight: 700; font-style: italic; font-size: 272px; fill: var(--white); }
  .subtitle { font-weight: 400; font-size: 60px; fill: var(--ink); }
  .testimony { font-weight: 700; font-size: 112px; fill: var(--ink); }
  .rule { stroke: var(--gold); stroke-width: 3; }
  .format-note { font-weight: 700; font-size: 26px; fill: var(--white); }
</style>
</head>
<body>
  <main class="cover">
    <svg class="cover-art" viewBox="0 0 1200 1200" xmlns="http://www.w3.org/2000/svg">
      <rect class="frame" x="49" y="49" width="1102" height="1102"/>

      <text class="series-title" x="600" y="280" text-anchor="middle">Q.I.V.A.</text>

      <g class="main-title">
        <text class="place" x="256" y="568" textLength="732" lengthAdjust="spacingAndGlyphs">HALBROOK</text>
        <text class="initial" x="236" y="772" textLength="166" lengthAdjust="spacingAndGlyphs">T</text>
        <text class="subtitle" x="442" y="632" textLength="538" lengthAdjust="spacing">Grand Jury</text>
        <text class="testimony" x="370" y="736" textLength="610" lengthAdjust="spacingAndGlyphs">ESTIMONY</text>
      </g>

      <line class="rule" x1="478" y1="1046" x2="746" y2="1046"/>
      <text class="format-note" x="322" y="1102" textLength="560" lengthAdjust="spacing">Unabridged   CD   format</text>
    </svg>
  </main>
</body>
</html>
```